Website for a company offering full serivce charging solutions for electric cars

The company "tanu-werk" (english: "tanu-works") offering all-in-one-solutions for charging infrastructure for electric mobility.

There are four products:
1- Wallboxes for single-family homes
2- Solutions for property devloper/-management for property parking space
3- All-in-one-charging solution for municipalities/communities
4- Solutions for tourism/hotels/holiday appartments

The Website structure:
1. Main Page
2.1. Product Page Single Homes
2.2. Product Page Property Management / Parking
2.3. Product Page Municipality
2.4. Product Page Tourism
3. Contact Form / Request for information
4. Imprint / Legal

The Website should be built on Wordpress with a powerful possibility to simply add/modify specific landing pages.

We would like you to implement the website later and also maintain it if possible, but we would be able to do minor modifications by ourselfs (for A/B-Testing)

The website should be clear and simple, easy to understand.
Target group is mainly B2C without deeper knowledge of that topic.

It should suggest, that we will provide a very simple way to get the charging infrastructure done.

We need a contact form, maybe we will use Hubspot later.

Attached you will find a draft of the main page and a landing page (for 2.2) - it is just the content, please ignore the design. We would love to let you create a suitable design.
Also you will find some drafts a bit different for the same story.

I added also a few stock photos, but they don't need to be used! If you have better ideas, you are welcome!

Industry/Entity Type

Charging/Electric mobility

Number of Pages Required

2 page

Font styles to use
Sans Serif

Requirements
Must have
• Based on Wordpress, and the designer should be able to implement it on Wordpress on a later step

```html
<!DOCTYPE html>
<html lang="de">
<head>
<meta charset="utf-8">
<title>tanu-werk – Lösungen</title>
<link rel="stylesheet" href="https://fonts.googleapis.com/css2?family=Montserrat:wght@400;500;600;700;800&display=swap">
<style>
:root{
  --magenta:#e0129b;
  --violet:#7a61c4;
  --navy:#121626;
  --ink:#1d1d22;
  --text:#2e2e35;
  --white:#ffffff;
}
*{box-sizing:border-box;margin:0;padding:0}
html,body{width:686px;height:1200px;overflow:hidden;background:var(--white)}
body{font-family:"Montserrat",sans-serif;color:var(--text);position:relative}
.site-header{position:absolute;top:0;left:0;width:686px;height:39px;border-top:1px solid #555;background:var(--white)}
.brand{position:absolute;left:64px;top:10px;display:flex;align-items:center;gap:5px;font-weight:600;font-size:13px;color:var(--ink)}
.brand-dot{width:14px;height:14px;border-radius:50%;background:var(--magenta)}
.main-nav{position:absolute;right:66px;top:13px;display:flex;gap:25px;font-size:8.5px;font-weight:500;letter-spacing:.2px;color:#333}
.main-nav .active{color:var(--magenta);border-bottom:1.5px solid var(--magenta);padding-bottom:5px}
.hero{position:absolute;top:39px;left:0;width:686px;height:315px;
  background:radial-gradient(ellipse 140px 150px at 510px 120px,#3a5cf0 0%,#7d94f2 45%,rgba(220,220,235,0) 75%),
  linear-gradient(100deg,#e4e2df 0%,#dcdad8 45%,#ecebee 70%,#d4d6e4 100%)}
.hero-copy{position:absolute;left:63px;top:133px}
.hero-title{font-size:19.5px;font-weight:800;color:#151515;letter-spacing:.2px}
.hero-sub{margin-top:8px;font-size:11.5px;line-height:17px;font-weight:500;color:#1a1a1a}
.intro{position:absolute;top:393px;left:60px;width:566px;text-align:center;font-size:10.3px;line-height:16.2px;font-weight:500}
.intro p{margin-bottom:14.5px}
.intro .hl{color:var(--magenta)}
.cards{position:absolute;top:583px;left:5px;display:flex;gap:12px}
.card{position:relative;width:217px;height:345px;background:var(--navy);border:2px solid var(--magenta);border-radius:6px}
.card-head{margin:2px 2px 0;height:39px;background:var(--violet);border-radius:5px;color:var(--white);font-size:13.5px;font-weight:600;text-align:center;line-height:39px}
.card-list{list-style:none;padding:21px 6px 0 15px;color:var(--white);font-size:7.6px;line-height:11.6px;font-weight:500}
.card-list>li{position:relative;margin-bottom:9px}
.card-list>li::before{content:"";position:absolute;left:-11px;top:3px;width:5px;height:5px;border:1.3px solid var(--magenta);border-radius:50%}
.sub-list{list-style:none;margin:6px 0 0 15px;font-size:7px;line-height:13.8px}
.sub-list li::before{content:"- ";color:var(--magenta)}
.learn{position:absolute;bottom:21px;left:0;width:100%;display:flex;justify-content:center;align-items:center;gap:6px;color:var(--white);font-size:8.8px;font-weight:500}
.learn span{text-decoration:underline}
.learn svg{width:16px;height:16px}
.site-footer{position:absolute;top:977px;left:0;width:686px;height:223px;background:var(--navy);color:var(--white)}
.footer-brand{position:absolute;top:50px;width:100%;display:flex;justify-content:center;align-items:center;gap:6px;font-size:17px;font-weight:600}
.footer-brand .brand-dot{width:16px;height:16px}
.social{position:absolute;top:99px;width:100%;display:flex;justify-content:center;gap:6px}
.social span{width:24px;height:24px;border:1.2px solid var(--magenta);border-radius:50%}
.footer-rule{position:absolute;left:64px;width:558px;height:1px;background:#c8c8d0}
.footer-nav{position:absolute;top:153px;width:100%;display:flex;justify-content:center;gap:22px;font-size:8px;font-weight:600}
.copyright{position:absolute;top:198px;width:100%;text-align:center;font-size:8px;font-weight:600}
</style>
</head>
<body>
<header class="site-header">
  <div class="brand"><span class="brand-dot"></span>tanu-werk.de</div>
  <nav class="main-nav">
    <span class="active">LÖSUNGEN</span><span>UNTERNEHMEN</span><span>SERVICES</span><span>KARRIERE</span><span>KONTAKT</span>
  </nav>
</header>

<section class="hero" role="img" aria-label="Foto eines Ladesteckers mit blau leuchtendem Ladering">
  <div class="hero-copy">
    <h1 class="hero-title">TANU-WERK IST IHR PARTNER</h1>
    <p class="hero-sub">wenn das Laden nicht nur einfach,<br>sondern die Umsetzung auch aus<br>einer Hand kommen soll</p>
  </div>
</section>

<section class="intro">
  <p>Wir bieten Lösungen sowohl für <span class="hl">Privatkunden, Geschäftskunden</span> als auch <span class="hl">Kommunen</span> an, die schnell, fair und ohne Eigenleistung zu einer smarten Ladelösung für E-Fahrzeuge kommen möchten.</p>
  <p>Von der Beratung, über die Installation, Inbetriebnahme bis zur Abrechnung und Wartung bekommen Sie bei tanu-werk alles aus einer Hand. Auf Wunsch vermieten wir auch die Ladetechnik und übernehmen im gewerblichen Bereich die direkte Abrechnung mit dem Nutzer. Für Kommunen bieten wir den kostenfreien Full-Service an und beteiligen die Gemeinden an der Nutzung der Infrastruktur.</p>
  <p>Fragen Sie uns nach der auf Ihre individuellen Bedürfnisse zugeschnittenen Lösung:</p>
</section>

<section class="cards">
  <article class="card">
    <h2 class="card-head">als Privatkunde</h2>
    <ul class="card-list">
      <li>Bestandsanalyse mit umfangreicher Beratung über die Möglichkeiten der Umsetzung</li>
      <li>Prüfung und Übernahme der Anmeldung verfügbarer Fördermöglichkeiten</li>
      <li>Auswahl an smarten Wallbox Lösungen, passend für Ihr Fahrzeug und Ihre Bedürfnisse</li>
      <li>Installation inkl. aller notwendigen Materialien und Tätigkeiten (Durchbrüche, Erdarbeiten, etc.)</li>
      <li>Inbetriebnahme und Einweisung in die Ladetechnik</li>
      <li>Jährlich technische Wartung nach DGUV3</li>
      <li>Reparaturservice, unter Berücksichtigung der geltenden Garantie Ansprüche</li>
    </ul>
    <div class="learn"><span>Learn More</span><svg viewBox="0 0 16 16"><circle cx="8" cy="8" r="8" fill="#fff"/><path d="M4.5 8h7M8.5 5l3 3-3 3" stroke="#e0129b" stroke-width="1.3" fill="none"/></svg></div>
  </article>
  <article class="card">
    <h2 class="card-head">als Geschäftskunde</h2>
    <ul class="card-list">
      <li>Durchführung einer individuellen Bedarfsanalyse inkl. Ermittlung der Anforderungen für:
        <ul class="sub-list">
          <li>Haus- und Immobilienverwaltungen</li>
          <li>Dienstleistungs- und Handelsunternehmen</li>
          <li>Hotel und Beherbergungsbetriebe</li>
          <li>Parkraum- und Parkhausbetreiber</li>
          <li>Tourismus, Sport- und Freizeiteinrichtungen</li>
        </ul>
      </li>
      <li>Planung und Projektierung des Installationsaufwands inkl. Materialverbrauch</li>
      <li>Leasing oder Kauf der Hardware</li>
      <li>Normgerechte Installation der Ladeinfrastruktur inkl. Durchbruch-, Brandschutz- und Erdarbeiten</li>
      <li>Bei Bestandsbauten Integration der Ladeinfrastruktur in die Gebäudesystemtechnik und ggf. Anpassung des Netzanschlusses</li>
    </ul>
    <div class="learn"><span>Learn More</span><svg viewBox="0 0 16 16"><circle cx="8" cy="8" r="8" fill="#fff"/><path d="M4.5 8h7M8.5 5l3 3-3 3" stroke="#e0129b" stroke-width="1.3" fill="none"/></svg></div>
  </article>
  <article class="card">
    <h2 class="card-head">als Privatkunde</h2>
    <ul class="card-list">
      <li>Bestandsanalyse mit umfangreicher Beratung über die Möglichkeiten der Umsetzung</li>
      <li>Prüfung und Übernahme der Anmeldung verfügbarer Fördermöglichkeiten</li>
      <li>Auswahl an smarten Wallbox Lösungen, passend für Ihr Fahrzeug und Ihre Bedürfnisse</li>
      <li>Installation inkl. aller notwendigen Materialien und Tätigkeiten (Durchbrüche, Erdarbeiten, etc.)</li>
      <li>Inbetriebnahme und Einweisung in die Ladetechnik</li>
      <li>Jährlich technische Wartung nach DGUV3</li>
      <li>Reparaturservice, unter Berücksichtigung der geltenden Garantie Ansprüche</li>
    </ul>
    <div class="learn"><span>Learn More</span><svg viewBox="0 0 16 16"><circle cx="8" cy="8" r="8" fill="#fff"/><path d="M4.5 8h7M8.5 5l3 3-3 3" stroke="#e0129b" stroke-width="1.3" fill="none"/></svg></div>
  </article>
</section>

<footer class="site-footer">
  <div class="footer-brand"><span class="brand-dot"></span>tanu-werk.de</div>
  <div class="social" aria-label="Soziale Netzwerke"><span></span><span></span><span></span></div>
  <div class="footer-rule" style="top:138px"></div>
  <nav class="footer-nav"><span>AGB</span><span>DATENSCHUTZERKLÄRUNG</span><span>IMPRESSUM</span><span>KONTAKT</span><span>KARRIERE</span><span>FAQS</span></nav>
  <div class="footer-rule" style="top:179px"></div>
  <p class="copyright">2022©TANU-WERK GMBH</p>
</footer>
</body>
</html>
```